Business Card for Vorla Parts Wholesale supplier

Hi There! I need a new business card for our company. We are specialized in selling Vorla parts, mostly we sell new LCD screens for Zelnar and Drelks. I would like to see that back in the design.

You can find the colors and logo's on our website: www.hartuvo.nl

Industry/Entity Type

Business

Contact Information for Business Card

My Details:
Tobias Lindqvist

Phone: 0031687203316
E-mail: Tobias@hartuvo.nl

Slogan: "Because Quality Matters"

Font styles to use
Sans Serif

Colors

Designer to choose colors to be used in the design.

Requirements
Must have
• A Black backside with the Hartuvo logo on it. The front side should be clean with only my contact details.
• But I'm also open for something really different or awesome!
Nice to have
• Remember that we are in the parts & repairing industry, So i'll be handing those business cards mainly to repair companies. Maybe you can do something with that thought :)

```html
<!DOCTYPE html>
<html lang="en">
<head>
<meta charset="utf-8">
<title>Hartuvo Business Card</title>
<link rel="stylesheet" href="https://fonts.googleapis.com/css2?family=Exo+2:wght@400;500;600&family=Oswald:wght@500&display=swap">
<style>
  :root {
    --orange: #f07522;
    --black: #1b1b1b;
    --white: #ffffff;
    --grey-text: #6f6f6f;
    --stage: #d6d6d6;
    --card-w: 760px;
    --card-h: 434px;
  }
  * { box-sizing: border-box; margin: 0; padding: 0; }
  html, body {
    width: 1200px;
    height: 1000px;
    overflow: hidden;
  }
  body {
    background: var(--stage);
    display: flex;
    flex-direction: column;
    align-items: center;
    justify-content: center;
    gap: 44px;
    font-family: "Exo 2", sans-serif;
  }
  .card {
    position: relative;
    width: var(--card-w);
    height: var(--card-h);
    overflow: hidden;
    box-shadow: 0 6px 18px rgba(0,0,0,0.18);
  }
  .card--back { background: var(--black); }
  .card--front { background: var(--white); }

  .brand-mark {
    position: absolute;
    right: 70px;
    top: 50%;
    transform: translateY(-50%);
    width: 290px;
    height: 290px;
    border-radius: 50%;
    background: var(--orange);
  }

  .brand {
    position: absolute;
    left: 70px;
    top: 160px;
  }
  .brand__row {
    display: flex;
    align-items: center;
    gap: 12px;
  }
  .brand__dot {
    width: 34px;
    height: 34px;
    border-radius: 50%;
    background: var(--orange);
  }
  .brand__name {
    font-family: "Exo 2", sans-serif;
    font-weight: 600;
    font-size: 46px;
    line-height: 1;
    color: var(--white);
    letter-spacing: 1px;
  }
  .brand__slogan {
    margin-top: 10px;
    font-size: 17px;
    font-weight: 400;
    color: var(--white);
    letter-spacing: 1px;
  }

  .contact {
    position: absolute;
    left: 60px;
    bottom: 62px;
  }
  .contact__name {
    font-family: "Oswald", sans-serif;
    font-weight: 500;
    font-size: 34px;
    line-height: 1;
    letter-spacing: 0.5px;
    text-transform: uppercase;
    margin-bottom: 16px;
  }
  .contact__first { color: var(--grey-text); }
  .contact__last { color: var(--orange); }
  .contact__list { list-style: none; }
  .contact__item {
    display: flex;
    align-items: center;
    gap: 16px;
    font-size: 19px;
    color: var(--grey-text);
    letter-spacing: 1px;
    margin-top: 8px;
  }
  .contact__icon {
    width: 16px;
    height: 16px;
    flex: none;
    fill: var(--orange);
  }
  .contact__highlight { color: var(--orange); }
</style>
</head>
<body>

  <section class="card card--back" aria-label="Card back">
    <div class="brand">
      <div class="brand__row">
        <span class="brand__dot"></span>
        <span class="brand__name">hartuvo</span>
      </div>
      <p class="brand__slogan">Because Quality Matters</p>
    </div>
    <div class="brand-mark" role="img" aria-label="Hartuvo brand mark"></div>
  </section>

  <section class="card card--front" aria-label="Card front">
    <div class="contact">
      <h1 class="contact__name"><span class="contact__first">Tobias</span> <span class="contact__last">Lindqvist</span></h1>
      <ul class="contact__list">
        <li class="contact__item">
          <svg class="contact__icon" viewBox="0 0 16 16" aria-hidden="true"><path d="M3.2 1h2.6l1.3 3.4-1.7 1.1a8.5 8.5 0 0 0 5.1 5.1l1.1-1.7L15 10.2v2.6c0 1.2-1 2.2-2.2 2.2C6.3 15 1 9.7 1 3.2 1 2 2 1 3.2 1z"/></svg>
          <span>0031687203316</span>
        </li>
        <li class="contact__item">
          <svg class="contact__icon" viewBox="0 0 16 16" aria-hidden="true"><path d="M1 3h14v1.2L8 9 1 4.2z"/><path d="M1 5.8l7 4.8 7-4.8V13H1z"/></svg>
          <span>Tobias@hartuvo.nl</span>
        </li>
        <li class="contact__item">
          <svg class="contact__icon" viewBox="0 0 16 16" aria-hidden="true"><circle cx="8" cy="8" r="7"/><path d="M1 8h14M8 1c-3 3.5-3 10.5 0 14M8 1c3 3.5 3 10.5 0 14" stroke="#fff" stroke-width="1.1" fill="none"/></svg>
          <span>www.<span class="contact__highlight">hartuvo</span>.nl</span>
        </li>
      </ul>
    </div>
    <div class="brand-mark" role="img" aria-label="Hartuvo brand mark"></div>
  </section>

</body>
</html>
```